Business Card Design

New business card design

Target Market(s)

Residential & Commercial Property Managers

Industry/Entity Type

Plumbing Services

Contact Information for Business Card

Name - Rowan Keddle, title - Director, Phone Number - 0431 286 517, email - rowan@tbk-plumbing.com.au, Company ABN - 73 215 904 386,

Font styles to use
Sans Serif

Colors
0054AA
0677BA
7BADD7
CADEEF
E8F1F8

```html
<!DOCTYPE html>
<html lang="en">
<head>
<meta charset="utf-8">
<title>TBK Plumbing Services – Business Card</title>
<link rel="stylesheet" href="https://fonts.googleapis.com/css2?family=Montserrat:wght@400;500;700&display=swap">
<style>
  :root {
    --backdrop: #e4e2e3;
    --card-white: #ffffff;
    --ink: #1e232b;
    --accent: #2ea8e0;
  }
  * { margin: 0; padding: 0; box-sizing: border-box; }
  html, body { width: 1200px; height: 1108px; overflow: hidden; }
  body {
    background: var(--backdrop);
    font-family: "Montserrat", sans-serif;
    color: var(--ink);
    position: relative;
  }
  .card {
    position: absolute;
    left: 236px;
    width: 740px;
    height: 446px;
    overflow: hidden;
  }
  .card--front { top: 61px; background: var(--card-white); }
  .card--back { top: 580px; height: 441px; background: var(--ink); }

  .wordmark {
    position: absolute;
    display: flex;
    align-items: center;
    gap: 10px;
    white-space: nowrap;
  }
  .wordmark__dot {
    border-radius: 50%;
    background: var(--accent);
    flex: none;
  }
  .wordmark__name { font-weight: 500; letter-spacing: 0.01em; }

  .card--front .wordmark { left: 72px; top: 236px; width: 280px; }
  .card--front .wordmark__dot { width: 12px; height: 12px; }
  .card--front .wordmark__name { font-size: 19px; line-height: 1; color: var(--ink); }

  .card--back .wordmark { left: 0; right: 0; top: 214px; justify-content: center; gap: 18px; }
  .card--back .wordmark__dot { width: 24px; height: 24px; }
  .card--back .wordmark__name { font-size: 40px; line-height: 1; color: var(--card-white); }

  .divider {
    position: absolute;
    left: 371px; top: 150px;
    width: 2px; height: 186px;
    background: var(--ink);
  }
  .contact { position: absolute; left: 388px; top: 146px; }
  .contact__name { font-weight: 700; font-size: 27px; line-height: 1.2; }
  .contact__title { font-size: 16px; margin-top: 1px; }
  .contact__list { list-style: none; margin-top: 18px; font-size: 16.5px; }
  .contact__item { display: flex; align-items: center; gap: 10px; height: 31px; }
  .contact__item svg { width: 17px; height: 17px; fill: var(--ink); flex: none; }
  .contact__abn { font-size: 16.5px; margin-top: 2px; }
  .contact__abn b { font-weight: 700; }

  .card__band { position: absolute; left: 0; bottom: 0; }
  .card__line { position: absolute; right: 0; bottom: 0; width: 390px; height: 2px; background: var(--accent); }
</style>
</head>
<body>
  <section class="card card--front">
    <div class="wordmark">
      <span class="wordmark__dot"></span>
      <span class="wordmark__name">tbk plumbing services</span>
    </div>
    <div class="divider"></div>
    <div class="contact">
      <p class="contact__name">Rowan Keddle</p>
      <p class="contact__title">Director</p>
      <ul class="contact__list">
        <li class="contact__item">
          <svg viewBox="0 0 24 24"><path d="M6.6 10.8a15 15 0 0 0 6.6 6.6l2.2-2.2a1 1 0 0 1 1-.25 11.4 11.4 0 0 0 3.6.57 1 1 0 0 1 1 1V20a1 1 0 0 1-1 1A17 17 0 0 1 3 4a1 1 0 0 1 1-1h3.5a1 1 0 0 1 1 1c0 1.25.2 2.45.57 3.57a1 1 0 0 1-.25 1z"/></svg>
          <span>0431 286 517</span>
        </li>
        <li class="contact__item">
          <svg viewBox="0 0 24 24"><path d="M3 6h18v1.5l-9 5.5-9-5.5zM3 9.3l9 5.5 9-5.5V18H3z"/></svg>
          <span>rowan@tbk-plumbing.com.au</span>
        </li>
        <li class="contact__item">
          <svg viewBox="0 0 24 24"><circle cx="12" cy="12" r="9" fill="none" stroke="#1e232b" stroke-width="2.4"/><path d="M3 12h18M12 3c3 3 3 15 0 18M12 3c-3 3-3 15 0 18" fill="none" stroke="#1e232b" stroke-width="1.6"/></svg>
          <span>www.tbk-plumbing.com.au</span>
        </li>
      </ul>
      <p class="contact__abn"><b>ABN</b> - 73 215 904 386,</p>
    </div>
    <svg class="card__band" width="740" height="26" viewBox="0 0 740 26">
      <polygon points="0,0 375,0 357,26 0,26" fill="#1e232b"/>
      <polygon points="385,0 740,0 740,26 367,26" fill="#2ea8e0"/>
    </svg>
  </section>

  <section class="card card--back">
    <div class="wordmark">
      <span class="wordmark__dot"></span>
      <span class="wordmark__name">tbk plumbing services</span>
    </div>
    <div class="card__line"></div>
  </section>
</body>
</html>
```